Southern Plantskills Academy needs a modern website that oozes professionalism

Our current website is boring and looks like everyone elses. We need a modern website that says we are the best at plant operator training. We use Brontovex and Hiraketo equipment for our training. We train all over Australia in Civil Construction, Mining and Quarrying. We want to be the "Go to" website for all plant operator training in Australia.

Industry/Entity Type

Heavy Machinery Training

Colors
0054AA
0677BA
7BADD7
CADEEF
E8F1F8
FFF300
FFF600
FEFA6F
FFFEC7
FFFEE8

```html
<!DOCTYPE html>
<html lang="en">
<head>
<meta charset="utf-8">
<title>Southern Plantskills Academy</title>
<link href="https://fonts.googleapis.com/css2?family=Fira+Sans:wght@400;500;600;700&family=Open+Sans:wght@400;600;700&display=swap" rel="stylesheet">
<style>
:root{
  --navy:#0c2340;
  --navy-2:#143259;
  --blue:#1b4a8a;
  --yellow:#fcc70d;
  --ink:#2b2b2b;
  --muted:#4a4a4a;
  --light:#f3f3f3;
  --footer:#1d2127;
  --white:#fff;
}
*{margin:0;padding:0;box-sizing:border-box}
html,body{width:1200px;height:4703px;overflow:hidden}
body{position:relative;font-family:"Open Sans",sans-serif;color:var(--ink);background:#fff}
.abs{position:absolute}
h1,h2,h3,h4{font-family:"Fira Sans",sans-serif;font-weight:600}
.section-title{position:absolute;left:0;width:100%;text-align:center;color:var(--blue);font-size:30px;letter-spacing:.5px}
.section-sub{position:absolute;left:50%;transform:translateX(-50%);width:520px;text-align:center;font-size:13px;line-height:22px;color:var(--muted)}
.btn{position:absolute;display:flex;align-items:center;justify-content:center;background:var(--yellow);color:#fff;font-family:"Fira Sans",sans-serif;font-weight:600;font-size:11px;letter-spacing:.6px;text-transform:uppercase;border-radius:2px}
.photo{position:absolute}

/* header */
.topbar{position:absolute;left:393px;top:0;width:807px;height:33px;background:var(--navy)}
.topbar-edge{position:absolute;left:360px;top:0}
.topbar-item{position:absolute;top:9px;font-size:9px;color:#fff}
.social-dot{display:inline-block;width:7px;height:7px;border-radius:50%;background:#fff;margin-left:5px;vertical-align:middle}
.quote-btn{position:absolute;left:842px;top:6px;width:110px;height:18px;border-top:3px solid var(--yellow);font-size:9px;font-weight:700;color:var(--yellow);text-align:center;line-height:16px}
.nav{position:absolute;left:0;top:33px;width:1200px;height:47px;background:#fff;border-bottom:1px solid #e6e6e6}
.nav a{position:absolute;top:15px;font-size:11px;color:#666;text-decoration:none}
.nav a.active{color:var(--blue);font-weight:700}
.brand{position:absolute;left:124px;top:22px;display:flex;align-items:center;gap:8px}
.brand-mark{width:30px;height:30px;border-radius:50%;background:var(--navy)}
.brand-name{font-family:"Fira Sans",sans-serif;font-weight:700;font-size:11px;line-height:13px;color:var(--navy);text-transform:uppercase}

/* hero */
.hero{position:absolute;left:0;top:80px;width:1200px;height:683px;background:linear-gradient(180deg,#4d5259 0%,#3a3a36 45%,#4b4031 75%,#2e2a25 100%)}
.hero-welcome{position:absolute;left:111px;top:190px;font-size:12px;color:#fff}
.hero-welcome::after{content:"";position:absolute;left:74px;top:8px;width:46px;height:1px;background:#fff}
.hero h1{position:absolute;left:111px;top:220px;font-size:40px;line-height:58px;color:#fff;letter-spacing:.5px}
.hero p{position:absolute;left:111px;top:352px;width:420px;font-size:13px;line-height:21px;color:#fff}

/* why */
.why-card{position:absolute;top:970px;width:232px;height:215px;background:#fff;box-shadow:0 2px 14px rgba(0,0,0,.1);text-align:center}
.why-card svg{position:absolute;left:96px;top:33px}
.why-card h3{position:absolute;top:88px;left:0;width:100%;font-size:18px;line-height:25px;color:var(--blue)}
.why-card p{position:absolute;top:147px;left:24px;right:24px;font-size:13px;line-height:22px;color:var(--muted)}
.why-card.featured{background:var(--navy)}
.why-card.featured h3,.why-card.featured p{color:#fff}

/* training */
.training-bg{position:absolute;left:281px;top:1322px;width:919px;height:466px;background:var(--navy)}
.training h2{position:absolute;left:632px;top:1410px;font-size:31px;color:#fff;letter-spacing:.4px}
.training p{position:absolute;left:632px;width:440px;font-size:12.5px;line-height:22px;color:#fff}

/* services */
.service-photo{position:absolute;top:2063px;width:320px;height:234px}
.service-box{position:absolute;top:2239px;width:284px;height:201px;background:#fff;box-shadow:0 2px 14px rgba(0,0,0,.1);padding:26px 38px 0}
.service-box h3{font-size:22px;color:var(--blue);margin-bottom:10px}
.service-box p{font-size:13px;line-height:22px;color:var(--muted)}
.service-box .more{margin-top:12px;font-size:10.5px;font-weight:700;color:var(--yellow);letter-spacing:.4px}
.service-box.featured{background:var(--navy)}
.service-box.featured h3,.service-box.featured p,.service-box.featured .more{color:#fff}

/* cta */
.cta{position:absolute;left:0;top:2511px;width:1200px;height:297px;background:linear-gradient(90deg,#2b3440 0%,#3b3a38 50%,#4a3a2a 100%)}
.cta-phone{position:absolute;left:0;width:100%;top:52px;text-align:center;color:#fff;font-family:"Fira Sans",sans-serif;font-size:22px;font-weight:500}
.cta h2{position:absolute;left:0;width:100%;top:92px;text-align:center;color:#fff;font-size:29px;letter-spacing:.4px}
.cta p{position:absolute;left:50%;transform:translateX(-50%);top:143px;width:480px;text-align:center;color:#fff;font-size:13px;line-height:22px}
.cta-btn{position:absolute;left:517px;top:212px;width:172px;height:41px;border:1px solid #fff;border-radius:3px;color:#fff;font-family:"Fira Sans",sans-serif;font-size:11px;font-weight:600;display:flex;align-items:center;justify-content:center;letter-spacing:.5px}

/* projects */
.project-side{position:absolute;top:3026px;height:352px}
.project-main{position:absolute;left:366px;top:3026px;width:476px;height:352px;background:linear-gradient(160deg,#5d6f86 0%,#3e5474 50%,#233a5c 100%)}
.project-main h3{position:absolute;left:33px;top:220px;color:#fff;font-size:19px}
.project-main .date{position:absolute;left:33px;top:248px;color:#fff;font-size:9px}
.project-main p{position:absolute;left:33px;top:268px;width:370px;color:#fff;font-size:10px;line-height:15px}

/* contact */
.contact-wrap{position:absolute;left:0;top:3448px;width:1200px;height:807px;background:var(--light)}
.contact-info{position:absolute;left:91px;top:3658px;width:510px;height:458px;background:linear-gradient(180deg,#3a5479 0%,#2c4a74 50%,#223f6a 100%)}
.contact-info .t{position:absolute;left:86px;color:#fff}
.contact-form{position:absolute;left:601px;top:3658px;width:504px;height:458px;background:#fff}
.field{position:absolute;left:86px;width:332px;height:32px;background:#f1f1f1;font-size:9px;color:#777;padding:10px 14px}
.round{display:inline-block;width:24px;height:24px;border-radius:50%;border:1px solid rgba(255,255,255,.6);margin-right:13px;vertical-align:middle}

/* info band */
.info-band{position:absolute;left:66px;top:4202px;width:1068px;height:102px;background:var(--yellow);border-radius:6px;z-index:2}
.info-item{position:absolute;top:26px;color:#fff}
.info-item h4{font-size:18px;font-weight:500;margin-bottom:6px}
.info-item p{font-size:12px}

/* footer */
.footer{position:absolute;left:0;top:4255px;width:1200px;height:448px;background:var(--footer);color:#fff}
.footer h4{position:absolute;top:133px;font-size:18px;font-weight:600}
.footer .rule{position:absolute;top:164px;width:32px;height:2px;background:var(--yellow)}
.footer a,.footer .link{position:absolute;color:#fff;font-size:13px;text-decoration:underline}
.newsletter{position:absolute;left:796px;top:254px;width:338px;height:52px;background:#fff;border-radius:3px}
.newsletter span{position:absolute;left:16px;top:18px;font-size:12px;font-weight:600;color:#333}
.newsletter .go{position:absolute;right:0;top:0;width:64px;height:52px;background:var(--yellow);border-radius:0 3px 3px 0}
.bottom-bar{position:absolute;left:0;top:383px;width:1200px;height:1px;background:#3a3f46}
.foot-brand{position:absolute;left:66px;top:383px;width:172px;height:65px;background:var(--yellow);display:flex;align-items:center;justify-content:center;gap:8px}
.foot-social{position:absolute;top:383px;width:58px;height:65px;border-left:1px solid #3a3f46;display:flex;align-items:center;justify-content:center}
.foot-social i{width:10px;height:10px;border-radius:50%;border:1px solid #6a7079}
</style>
</head>
<body>

<!-- Header -->
<svg class="topbar-edge" width="40" height="33" viewBox="0 0 40 33"><path d="M0 0H40V33H12Z" fill="#0c2340"/></svg>
<div class="topbar">
  <div class="topbar-item" style="left:75px">
    <svg width="8" height="10" viewBox="0 0 8 10" style="vertical-align:middle"><path d="M4 0a4 4 0 0 1 4 4c0 3-4 6-4 6S0 7 0 4a4 4 0 0 1 4-4z" fill="#fff"/></svg>
    &nbsp;48 Quarry Rd, Ballarat VIC 3350
  </div>
  <div class="topbar-item" style="left:310px">Follow Us: <span class="social-dot"></span><span class="social-dot"></span><span class="social-dot"></span></div>
  <div class="quote-btn" style="left:449px">GET QUOTATION</div>
</div>
<nav class="nav">
  <div class="brand" style="top:-11px"><span class="brand-mark"></span><span class="brand-name">Southern<br>Plantskills Academy</span></div>
  <a class="active" style="left:390px">Home</a>
  <a style="left:483px">About Us</a>
  <a style="left:577px">Services</a>
  <a style="left:671px">Gallery</a>
  <a style="left:759px">Our Team</a>
  <a style="left:864px">Contact Us</a>
</nav>

<!-- Hero -->
<section class="hero" role="img" aria-label="Large yellow mining haul truck loaded with rock on a dusty quarry road at dusk">
  <div class="hero-welcome">Welcome</div>
  <h1>Empowering Operators,<br>Fueling Progress</h1>
  <p>Lorem ipsum dolor sit amet, consectetur adipiscing elit, sed do eiusmod tempor incididunt ut labore et dolore magna Lorem ipsum dolor sit amet, consectetur adipiscing elit, sed do eiusmod tempor incididunt ut labore et dolore magna</p>
  <div class="btn" style="left:111px;top:461px;width:192px;height:40px">Discover more</div>
</section>

<!-- Why we are the best -->
<h2 class="section-title" style="top:842px">Why We AreThe Best</h2>
<p class="section-sub" style="top:895px">Lorem ipsum dolor sit amet, consectetur adipiscing elit, sed do eiusmod tempor incididunt ut labore et dolore magna aliqua. Ut enim ad min</p>

<div class="why-card" style="left:93px">
  <svg width="40" height="40" viewBox="0 0 40 40" fill="none" stroke="#fcc70d" stroke-width="2"><circle cx="20" cy="20" r="6"/><path d="M20 4v5M20 31v5M4 20h5M31 20h5M8.7 8.7l3.5 3.5M27.8 27.8l3.5 3.5M8.7 31.3l3.5-3.5M27.8 12.2l3.5-3.5"/><circle cx="20" cy="20" r="12"/></svg>
  <h3 style="top:88px">Expertise</h3>
  <p>Lorem ipsum dolor sit amet, consectetur adipiscing</p>
</div>
<div class="why-card featured" style="left:352px">
  <svg width="40" height="40" viewBox="0 0 40 40" fill="none" stroke="#fff" stroke-width="2"><circle cx="18" cy="18" r="11"/><circle cx="26" cy="26" r="5"/><path d="M12 18h12M18 12v12"/></svg>
  <h3 style="top:88px">Comprehensive<br>Services</h3>
  <p style="top:147px">Lorem ipsum dolor sit amet, consectetur adipiscing</p>
</div>
<div class="why-card" style="left:612px">
  <svg width="40" height="40" viewBox="0 0 40 40" fill="none" stroke="#fcc70d" stroke-width="2"><circle cx="20" cy="14" r="7"/><path d="M7 36c0-8 6-12 13-12s13 4 13 12z"/></svg>
  <h3 style="top:88px">Experienced</h3>
  <p>Lorem ipsum dolor sit amet, consectetur adipiscing</p>
</div>
<div class="why-card" style="left:873px">
  <svg width="40" height="40" viewBox="0 0 40 40" fill="none" stroke="#fcc70d" stroke-width="2"><path d="M20 5l4.6 9.4 10.4 1.5-7.5 7.3 1.8 10.3L20 28.6l-9.3 4.9 1.8-10.3-7.5-7.3 10.4-1.5z"/></svg>
  <h3 style="top:88px">Quality<br>Assurance</h3>
  <p>Lorem ipsum dolor sit amet, consectetur adipiscing</p>
</div>
<div class="btn" style="left:521px;top:1224px;width:172px;height:40px">Learn more about</div>

<!-- Training -->
<section class="training">
  <div class="training-bg"></div>
  <div class="photo" style="left:0;top:1384px;width:581px;height:448px;background:linear-gradient(135deg,#cfd8df 0%,#a9b3b8 35%,#d9733a 60%,#7a6a4a 100%)" role="img" aria-label="Plant operator in hard hat and hi-vis vest directing beside a yellow wheel loader"></div>
  <h2>Training Meets Transformation</h2>
  <p style="top:1464px">Lorem ipsum dolor sit amet, consectetur adipiscing elit, sed do e iusmod tempor incididunt ut labore et dolore magna aliqua. Ut eni m ad minim veniam, quis nostrud ex</p>
  <p style="top:1539px">Lorem ipsum dolor sit amet, consectetur adipiscing elit, sed do eius mod tempor incididunt ut labore et dolore magna aliqua. Ut enim a d minim veniam, quis nostrud exercitation ullamco laboris nisi ut aliq uip ex ea commodo consequat. Duis aute iru</p>
  <div class="btn" style="left:632px;top:1651px;width:172px;height:40px">Learn more about</div>
</section>

<!-- What we do -->
<h2 class="section-title" style="top:1910px">What We Do</h2>
<p class="section-sub" style="top:1965px">Lorem ipsum dolor sit amet, consectetur adipiscing elit, sed do eiusmod tempor incididunt ut labore et dolore magna aliqua. Ut enim ad min</p>

<div class="service-photo" style="left:93px;background:linear-gradient(135deg,#cfd8e0 0%,#8d9aa6 45%,#d6a72a 100%)" role="img" aria-label="Civil construction worker with safety glasses in front of an excavator"></div>
<div class="service-photo" style="left:440px;background:linear-gradient(135deg,#e6c7a0 0%,#d98a4a 45%,#b98a5a 100%)" role="img" aria-label="Mining worker in hard hat at a rocky mine site"></div>
<div class="service-photo" style="left:787px;background:linear-gradient(135deg,#d2a36a 0%,#b8804a 50%,#8a5a30 100%)" role="img" aria-label="Yellow excavator digging in a sandy quarry"></div>

<div class="service-box" style="left:111px"><h3>Civil Construction</h3><p>Lorem ipsum dolor sit amet, cons ectetur adipiscing elit, sed do eius mod tempor incididunt ut labore et dolore magna aliqua.</p><div class="more">LEARN MORE</div></div>
<div class="service-box featured" style="left:458px"><h3>Mining</h3><p>Lorem ipsum dolor sit amet, cons ectetur adipiscing elit, sed do eius mod tempor incididunt ut labore et dolore magna aliqua.</p><div class="more">LEARN MORE</div></div>
<div class="service-box" style="left:805px"><h3>Quarrying</h3><p>Lorem ipsum dolor sit amet, cons ectetur adipiscing elit, sed do eius mod tempor incididunt ut labore et dolore magna aliqua.</p><div class="more">LEARN MORE</div></div>

<!-- CTA -->
<section class="cta" role="img" aria-label="Dim close-up of heavy machinery at dusk behind a dark overlay">
  <div class="cta-phone">
    <svg width="34" height="34" viewBox="0 0 24 24" fill="none" stroke="#fff" stroke-width="1.3" style="vertical-align:middle;margin-right:10px"><path d="M5 3h4l2 5-2.5 1.5a11 11 0 0 0 6 6L16 13l5 2v4a2 2 0 0 1-2 2A16 16 0 0 1 3 5a2 2 0 0 1 2-2z"/></svg>1800 555 014
  </div>
  <h2>Where Operators Thrive and Industries Flourish</h2>
  <p>Lorem ipsum dolor sit amet, consectetur adipiscing elit, sed do eiusmod tempor incididunt ut labore et dolore magna aliqua.</p>
  <div class="cta-btn">CONTACT US NOW</div>
</section>

<!-- Projects -->
<h2 class="section-title" style="top:2885px">Our Recent Projects</h2>
<p class="section-sub" style="top:2940px">Lorem ipsum dolor sit amet, consectetur adipiscing elit, sed do eiusmod tempor incididunt ut labore et dolore magna aliqua. Ut enim ad min</p>

<div class="project-side" style="left:124px;width:223px;clip-path:polygon(0 22%,100% 0,100% 100%,0 78%);background:linear-gradient(160deg,#b9c3cc 0%,#d8a35a 55%,#6a5a3e 100%)" role="img" aria-label="Wheel loader on a construction site at sunset"></div>
<div class="project-main" role="img" aria-label="Smiling operator in hard hat and hi-vis vest in front of a wheel loader">
  <h3>Lorem Ipsum dolor sit amet</h3>
  <div class="date">08.08.2024</div>
  <p>Veniam culpa laborum enim laborum aliqua consequat irure ea mollit minim cupidat veniam culpa laborum enim laborum aliqua mollit minim cupidat</p>
</div>
<div class="project-side" style="left:858px;width:221px;clip-path:polygon(0 0,100% 22%,100% 78%,0 100%);background:linear-gradient(170deg,#a8b0b8 0%,#8a7a62 45%,#4e4334 100%)" role="img" aria-label="Excavator working on a cleared earthworks site"></div>

<!-- Contact -->
<section class="contact-wrap"></section>
<h2 class="section-title" style="top:3508px">Contact Us</h2>
<p class="section-sub" style="top:3563px">Lorem ipsum dolor sit amet, consectetur adipiscing elit, sed do eiusmod tempor incididunt ut labore et dolore magna aliqua. Ut enim ad min</p>

<div class="contact-info" role="img" aria-label="Operators and machinery on site behind a blue overlay">
  <div class="t" style="top:66px;font-size:15px;font-weight:600">CONTACT US</div>
  <div class="t" style="top:104px;font-size:21px">Call: 03 5550 1420</div>
  <div class="t" style="top:138px;font-size:11px;font-weight:600">info@plantskills.example</div>
  <div class="t" style="top:180px;font-size:11px;line-height:19px"><b>Address:</b><br>48 QUARRY RD<br>BALLARAT VIC 3350</div>
  <div class="t" style="top:266px;font-size:11px;line-height:19px"><b>Operating Hours</b><br>Monday to Saturday: 9:00 - 18:00<br>Sunday: Closed</div>
  <div class="t" style="top:369px"><span class="round"></span><span class="round" style="background:#fff"></span><span class="round"></span><span class="round"></span></div>
</div>
<div class="contact-form">
  <div class="abs" style="left:86px;top:58px;font-family:'Fira Sans',sans-serif;font-weight:600;font-size:16px;color:var(--blue)">FREE CONSULTATION</div>
  <div class="field" style="top:109px">Your Name</div>
  <div class="field" style="top:159px">Email</div>
  <div class="field" style="top:208px">Phone</div>
  <div class="field" style="top:257px;height:95px">Message ...</div>
  <div class="btn" style="left:86px;top:369px;width:109px;height:36px">Submit</div>
</div>

<!-- Info band -->
<div class="info-band">
  <svg class="abs" style="left:40px;top:28px" width="50" height="46" viewBox="0 0 50 46" fill="none" stroke="#fff" stroke-width="1.6"><path d="M25 4a10 10 0 0 1 10 10c0 8-10 18-10 18S15 22 15 14A10 10 0 0 1 25 4z"/><circle cx="25" cy="14" r="4"/><path d="M12 28L2 44h46L38 28"/></svg>
  <div class="info-item" style="left:109px"><h4>Address</h4><p>27 Haulage St, Ballarat</p></div>
  <svg class="abs" style="left:398px;top:28px" width="48" height="48" viewBox="0 0 24 24" fill="none" stroke="#fff" stroke-width="1"><path d="M5 3h4l2 5-2.5 1.5a11 11 0 0 0 6 6L16 13l5 2v4a2 2 0 0 1-2 2A16 16 0 0 1 3 5a2 2 0 0 1 2-2z"/></svg>
  <div class="info-item" style="left:465px"><h4>Phone</h4><p>+61 3 5550 1420</p></div>
  <svg class="abs" style="left:756px;top:28px" width="48" height="48" viewBox="0 0 48 48" fill="none" stroke="#fff" stroke-width="1.6"><path d="M4 20l20-14 20 14v24H4z"/><path d="M4 20l20 14 20-14"/><circle cx="24" cy="18" r="5"/></svg>
  <div class="info-item" style="left:825px"><h4>Email Contact</h4><p>info@plantskills.example</p></div>
</div>

<!-- Footer -->
<footer class="footer">
  <h4 style="left:66px">About Us</h4><div class="rule" style="left:66px"></div>
  <p class="abs" style="left:66px;top:196px;width:310px;font-size:13px;line-height:33px">Lorem ipsum dolor sit amet, consectetur adipi elit, sed do eiusmod tempor incididunt ut lab dolore magna aliqua.</p>
  <span class="link" style="left:66px;top:301px;color:var(--yellow);font-size:15px">Read More</span>

  <h4 style="left:433px">Useful Links</h4><div class="rule" style="left:433px"></div>
  <a style="left:433px;top:196px">About Us</a>
  <a style="left:433px;top:229px">Projects</a>
  <a style="left:433px;top:262px">Blog</a>
  <a style="left:433px;top:296px">Contact Us</a>
  <a style="left:610px;top:196px">Services</a>
  <a style="left:610px;top:229px">Shop</a>
  <a style="left:610px;top:262px">Privacy Policy</a>
  <a style="left:610px;top:296px">Help Desk</a>

  <h4 style="left:796px">Useful Links</h4><div class="rule" style="left:796px"></div>
  <p class="abs" style="left:796px;top:196px;width:330px;font-size:13.5px;line-height:25px">If you have any questions, Subscribe to our newsletter to get our latest products</p>
  <div class="newsletter"><span>Email</span><div class="go"><svg style="position:absolute;left:22px;top:16px" width="20" height="20" viewBox="0 0 20 20" fill="none" stroke="#fff" stroke-width="2"><path d="M2 10h15M11 4l6 6-6 6"/></svg></div></div>

  <div class="bottom-bar"></div>
  <div class="foot-brand"><span style="width:16px;height:16px;border-radius:50%;background:#fff"></span><span style="font-family:'Fira Sans',sans-serif;font-weight:700;font-size:10px;line-height:12px;color:#fff">SOUTHERN<br>PLANTSKILLS</span></div>
  <div class="foot-social" style="left:901px"><i></i></div>
  <div class="foot-social" style="left:959px"><i></i></div>
  <div class="foot-social" style="left:1017px"><i></i></div>
  <div class="foot-social" style="left:1075px;border-right:1px solid #3a3f46"><i></i></div>
</footer>

</body>
</html>
```